Personal training and nutrition business needs business card design

We need a business card that outlays our services and invites potential customers to join our team and take the first step to a healthier and more enjoyable life. We cater for any level of fitness and specialize in weight loss and conditioning, strength training, muscle gain and strength endurance. Whether you are just starting off or need some help getting to the next level of your journey we are here to get the job done.
We specialize in one on one or one on two personal training sessions and each program will be custom made to suit individual fitness goals of our clients

```html
<!DOCTYPE html>
<html lang="en">
<head>
<meta charset="utf-8">
<title>Pace &amp; Poise — Business Card</title>
<link href="https://fonts.googleapis.com/css2?family=Roboto:wght@400;900&family=Oswald:wght@500&display=swap" rel="stylesheet">
<style>
  :root {
    --bg: #2a2a2a;
    --card: #efefef;
    --card-light: #f7f7f7;
    --ink: #141414;
    --text: #2e2e2e;
    --violet: #6a3f97;
    --orchid: #9b5aa0;
    --accent: #8a4ea0;
  }
  html, body {
    margin: 0; padding: 0;
    width: 1200px; height: 1138px;
    overflow: hidden;
    background: var(--bg);
  }
  .canvas { position: relative; width: 1200px; height: 1138px; }
  .card {
    position: absolute;
    left: 274px; width: 622px; height: 376px;
    border-radius: 16px;
    background: linear-gradient(135deg, var(--card-light), var(--card));
    overflow: hidden;
    font-family: "Roboto", sans-serif;
  }
  .card--front { top: 186px; }
  .card--back { top: 608px; left: 276px; width: 618px; height: 374px; }

  /* front */
  .front-mark {
    position: absolute; left: 267px; top: 56px;
    width: 88px; height: 88px; border-radius: 50%;
    background: linear-gradient(135deg, var(--violet), var(--orchid));
  }
  .brand {
    font-family: "Roboto", sans-serif;
    font-weight: 900; color: var(--ink);
    text-transform: uppercase; letter-spacing: 1px; margin: 0;
  }
  .front-brand {
    position: absolute; left: 0; right: 0; top: 208px;
    text-align: center; font-size: 40px; line-height: 40px;
  }
  .tagline {
    font-family: "Oswald", sans-serif; font-weight: 500;
    color: var(--accent); text-transform: uppercase;
    letter-spacing: 1px; margin: 0;
  }
  .front-tagline {
    position: absolute; left: 0; right: 0; top: 252px;
    text-align: center; font-size: 13px;
  }
  .front-web {
    position: absolute; left: 0; right: 0; top: 322px;
    display: flex; justify-content: center; align-items: center; gap: 18px;
    font-size: 15px; color: var(--ink);
  }
  .rule { width: 70px; height: 2px; background: var(--ink); border-radius: 2px; }
  .hl { color: var(--accent); }
  .front-band {
    position: absolute; left: 0; right: 0; bottom: 0; height: 10px;
    background: linear-gradient(90deg, var(--orchid), var(--violet));
  }

  /* back */
  .back-deco {
    position: absolute; left: -120px; top: 14px;
    width: 470px; height: 350px;
  }
  .back-brand {
    position: absolute; right: 38px; top: 30px;
    text-align: right; font-size: 31px; line-height: 33px;
  }
  .back-tagline {
    position: absolute; right: 38px; top: 98px;
    font-size: 8px; letter-spacing: 0.6px;
  }
  .person { position: absolute; right: 38px; top: 156px; text-align: right; }
  .person-name {
    font-family: "Oswald", sans-serif; font-weight: 500;
    color: var(--accent); font-size: 22px; margin: 0; line-height: 28px;
  }
  .person-role { font-size: 15px; color: var(--text); margin: 2px 0 0; }
  .contacts {
    position: absolute; right: 18px; top: 234px;
    list-style: none; margin: 0; padding: 0;
    font-size: 15px; color: var(--text);
  }
  .contacts li {
    display: flex; justify-content: flex-end; align-items: center;
    gap: 10px; height: 24px;
  }
  .contacts svg { width: 13px; height: 13px; fill: var(--accent); }
  .address {
    position: absolute; right: 38px; top: 314px;
    font-size: 15px; color: var(--text); margin: 0;
  }
  .edge-dot {
    position: absolute; right: -26px; top: 152px;
    width: 52px; height: 52px; border-radius: 50%;
    background: linear-gradient(135deg, var(--violet), var(--orchid));
  }
</style>
</head>
<body>
<main class="canvas">
  <section class="card card--front" aria-label="Card front">
    <div class="front-mark"></div>
    <h1 class="brand front-brand">Pace &amp; Poise</h1>
    <p class="tagline front-tagline">Personal training.&nbsp; Nutrition. Motivation</p>
    <div class="front-web">
      <span class="rule"></span>
      <span>www.<span class="hl">pace</span>and<span class="hl">poise</span>.com</span>
      <span class="rule"></span>
    </div>
    <div class="front-band"></div>
  </section>

  <section class="card card--back" aria-label="Card back">
    <svg class="back-deco" viewBox="0 0 470 350" role="img" aria-label="Large brand accent shape">
      <defs>
        <linearGradient id="decoGrad" x1="0" y1="1" x2="1" y2="0">
          <stop offset="0" stop-color="#6a3f97"/>
          <stop offset="1" stop-color="#9b5aa0"/>
        </linearGradient>
      </defs>
      <circle cx="235" cy="175" r="175" fill="url(#decoGrad)"/>
    </svg>

    <h2 class="brand back-brand">Pace &amp;<br>Poise</h2>
    <p class="tagline back-tagline">Personal training.&nbsp; Nutrition. Motivation</p>

    <div class="person">
      <p class="person-name">Dana Reyes</p>
      <p class="person-role">Personal Trainer</p>
    </div>

    <ul class="contacts">
      <li>+1 (555) 014-2286
        <svg viewBox="0 0 24 24" aria-hidden="true"><path d="M6.6 10.8a15 15 0 0 0 6.6 6.6l2.2-2.2a1 1 0 0 1 1-.25 11.4 11.4 0 0 0 3.6.57 1 1 0 0 1 1 1V20a1 1 0 0 1-1 1A17 17 0 0 1 3 4a1 1 0 0 1 1-1h3.5a1 1 0 0 1 1 1c0 1.25.2 2.45.57 3.57a1 1 0 0 1-.25 1z"/></svg>
      </li>
      <li>dana@paceandpoise.com
        <svg viewBox="0 0 24 24" aria-hidden="true"><path d="M2 5h20v14H2z M4 7v.5l8 5 8-5V7l-8 5z" fill-rule="evenodd"/></svg>
      </li>
      <li>www.<span class="hl">pace</span>and<span class="hl">poise</span>.com
        <svg viewBox="0 0 24 24" aria-hidden="true"><path d="M12 2a10 10 0 1 0 0 20 10 10 0 0 0 0-20zm0 2c.9 1.2 1.6 2.6 2 4h-4c.4-1.4 1.1-2.8 2-4zM4.3 14a8 8 0 0 1 0-4h3.4a16 16 0 0 0 0 4zm.8 2h3a14 14 0 0 0 1.4 3.4A8 8 0 0 1 5.1 16zm3-8h-3a8 8 0 0 1 4.4-3.4A14 14 0 0 0 8.1 8zM12 20c-.9-1.2-1.6-2.6-2-4h4c-.4 1.4-1.1 2.8-2 4zm2.3-6H9.7a14 14 0 0 1 0-4h4.6a14 14 0 0 1 0 4zm.2 5.4A14 14 0 0 0 15.9 16h3a8 8 0 0 1-4.4 3.4zm1.8-5.4a16 16 0 0 0 0-4h3.4a8 8 0 0 1 0 4zm-.4-6a14 14 0 0 0-1.4-3.4A8 8 0 0 1 18.9 8z"/></svg>
      </li>
    </ul>
    <p class="address">418 Maple Ridge Rd Austin Texas 78701</p>
    <div class="edge-dot"></div>
  </section>
</main>
</body>
</html>
```